Dorvik Electric Ltd

Looking for a single page website and Facebook page design. I am an electrical contractor based on Vancouver Island. I do service, custom homes, residential and commercial installations. My company just started out, so I don't have any pictures of installs yet. I have 25 years experience. I would like the colors to be my logo colors black and I have a black Brandt Halvard that will be my vehicle which I will have a wrap for.
Updates

I just posted the contest today, not sure why the deadline is the same day.

Industry/Entity Type

Electrician

Requirements
Must have
• Services provided, About me section, quote section,
Nice to have
• I am not quite sure yet, I need to see some designs first .

```html
<!DOCTYPE html>
<html lang="en">
<head>
<meta charset="utf-8">
<title>Dorvik Electric Ltd</title>
<link href="https://fonts.googleapis.com/css2?family=Raleway:wght@500;600;700;800;900&family=Open+Sans:wght@400;600&display=swap" rel="stylesheet">
<style>
:root{
  --yellow:#f0b31b;
  --yellow-deep:#e5a710;
  --ink:#141414;
  --text:#3a3a3a;
  --muted:#6b6b6b;
  --light:#f1f1f1;
  --white:#ffffff;
}
*{box-sizing:border-box;margin:0;padding:0}
html,body{width:1200px;height:4648px;overflow:hidden}
body{position:relative;background:var(--white);font-family:"Open Sans",Arial,sans-serif;color:var(--text)}
.abs{position:absolute}
.head{font-family:"Raleway",Arial,sans-serif}

/* header */
.site-header{left:0;top:0;width:1200px;height:99px;background:var(--white);z-index:5}
.nav-link{top:40px;font-family:"Raleway",Arial,sans-serif;font-size:16px;font-weight:500;color:var(--ink)}
.search-icon{left:920px;top:42px}
.btn-login{left:980px;top:31px;width:107px;height:40px;border-radius:20px;background:var(--yellow);font-family:"Raleway",sans-serif;font-weight:700;font-size:15px;color:var(--ink);display:flex;align-items:center;justify-content:center}
.brand-badge{left:492px;top:-50px;width:216px;height:220px;border-radius:50%;background:var(--white);z-index:6}
.brand-dot{left:562px;top:18px;width:76px;height:76px;border-radius:50%;border:5px solid var(--ink);z-index:7}
.brand-name{left:492px;top:102px;width:216px;text-align:center;font-family:"Raleway",sans-serif;font-weight:700;font-size:14px;color:var(--ink);z-index:7}

/* hero */
.hero-photo{left:0;top:99px;width:1200px;height:690px;background:radial-gradient(ellipse 520px 420px at 560px 470px,#ffe7a0 0%,#f3a445 14%,#c06a2e 38%,#7a3f22 62%,#3a2218 100%)}
.hero-shape{left:0;top:680px}
.hero-kicker{left:112px;top:192px;font-size:30px;font-weight:700;color:var(--white);letter-spacing:.5px}
.hero-kicker::after{content:"";display:inline-block;width:68px;height:3px;background:var(--white);margin-left:22px;vertical-align:middle}
.hero-title{left:108px;font-size:84px;font-weight:900;line-height:1}
.hero-title.one{top:250px;color:var(--white)}
.hero-title.two{top:352px;color:var(--yellow)}
.hero-copy{left:112px;top:454px;width:420px;font-size:15px;line-height:26px;color:var(--white)}
.btn{border-radius:22px;background:var(--yellow);font-family:"Raleway",sans-serif;font-weight:700;color:var(--ink);display:flex;align-items:center;justify-content:center}
.btn-start{left:112px;top:538px;width:144px;height:43px;font-size:14px}
.slider-dots{left:1124px;top:400px;display:flex;flex-direction:column;gap:7px}
.slider-dots span{width:12px;height:12px;border-radius:50%;background:var(--white)}
.slider-dots span.on{background:var(--yellow)}

/* about */
.about-photo-a{left:162px;top:866px;width:542px;height:416px;background:linear-gradient(120deg,#1f2229 0%,#4a4e58 30%,#8c8e94 52%,#3c4a62 70%,#6a7686 100%)}
.about-photo-b{left:112px;top:1101px;width:309px;height:253px;background:linear-gradient(170deg,#a9bfd8 0%,#d8dde2 30%,#9a8e80 60%,#5a4638 100%)}
.about-panel{left:600px;top:930px;width:520px;height:330px;background:var(--white)}
.eyebrow{font-family:"Raleway",sans-serif;font-weight:700;font-size:14px;color:var(--yellow)}
.about-eyebrow{left:637px;top:960px}
.mini-rule{left:640px;top:982px}
.about-title{left:635px;top:994px;font-size:31px;font-weight:600;color:var(--ink)}
.about-copy{left:637px;top:1054px;width:448px;font-size:15px;line-height:26px;text-align:justify;color:var(--text)}
.btn-learn{left:637px;top:1294px;width:145px;height:38px;font-size:14px}

/* section titles */
.section-title{left:0;width:1200px;text-align:center;font-family:"Raleway",sans-serif;font-weight:600;font-size:30px;color:var(--ink)}
.divider{left:500px;width:200px;height:20px}

/* services */
.services-band{left:0;top:1440px;width:1200px;height:683px;background:linear-gradient(100deg,#e9e9e9 0%,#f5f5f5 40%,#ecebe6 70%,#f3f3f3 100%)}
.services-strip{left:0;top:1643px}
.service-label{top:1778px;width:360px;text-align:center;font-family:"Raleway",sans-serif;font-weight:600;font-size:30px;color:var(--white);text-shadow:0 2px 6px rgba(0,0,0,.45)}
.service-plus{top:1840px;width:60px;height:60px;border-radius:50%;background:var(--yellow);box-shadow:0 0 0 6px rgba(240,179,27,.35);display:flex;align-items:center;justify-content:center;font-size:24px;font-weight:700;color:var(--ink)}

/* testimonials */
.testimonial-photo{left:1020px;top:2123px;width:180px;height:579px;background:linear-gradient(180deg,#4e4034 0%,#9a7a50 12%,#f4b820 28%,#e89a18 45%,#6a3a20 62%,#2a2220 80%,#c27a2a 100%)}
.quote-mark{left:0;width:1200px;top:2288px;text-align:center;font-family:Georgia,serif;font-weight:700;font-size:110px;line-height:110px;color:var(--yellow)}
.quote-copy{left:257px;top:2390px;width:686px;text-align:center;font-size:15px;line-height:26px;color:var(--text)}
.arrow{top:2434px}
.stars{left:0;width:1200px;top:2534px;text-align:center;color:var(--yellow);font-size:22px;letter-spacing:4px}
.client-name{left:0;width:1200px;top:2574px;text-align:center;font-family:"Raleway",sans-serif;font-weight:700;font-size:20px;color:var(--ink)}
.client-role{left:0;width:1200px;top:2604px;text-align:center;font-size:14px;color:var(--text)}

/* projects */
.projects-band{left:0;top:2702px;width:1200px;height:809px;background:linear-gradient(160deg,#f0b31b 0%,#e8aa14 50%,#d99c12 75%,#e9ac18 100%)}
.projects-band .section-title{color:var(--white)}
.project-tile{width:307px;height:253px;border-radius:18px}

/* blog */
.blog-feature{left:125px;top:3715px;width:462px;height:319px;background:linear-gradient(120deg,#3a3430 0%,#8a6e4a 30%,#e8b830 48%,#6a5e54 68%,#2e2e30 100%)}
.blog-card{left:159px;top:3895px;width:462px;height:199px;background:var(--white);border:1px solid #e0e0e0;box-shadow:0 4px 14px rgba(0,0,0,.08)}
.blog-date{font-size:12px;color:var(--muted);display:flex;align-items:center;gap:8px}
.blog-date::before{content:"";width:10px;height:10px;border-radius:50%;border:2px solid var(--yellow)}
.blog-title{font-family:"Raleway",sans-serif;font-weight:700;font-size:15px;color:var(--ink);line-height:26px}
.blog-copy{font-size:12px;line-height:19px;color:var(--text)}
.read-more{font-family:"Raleway",sans-serif;font-weight:700;font-size:14px;color:var(--yellow)}
.card-nav{width:30px;height:30px;display:flex;align-items:center;justify-content:center;color:var(--white);font-size:18px}
.blog-thumb{left:646px;width:190px;height:177px}

/* footer */
.footer-shape{left:0;top:4180px}
.footer-dot{left:155px;top:4322px;width:112px;height:112px;border-radius:50%;border:6px solid var(--yellow)}
.footer-brand{left:60px;top:4434px;width:302px;text-align:center;font-family:"Raleway",sans-serif;font-weight:700;font-size:17px;color:var(--white)}
.social{top:4502px;width:18px;height:18px;border-radius:50%;background:var(--white)}
.footer-title{top:4326px;font-family:"Raleway",sans-serif;font-weight:600;font-size:22px;color:var(--white)}
.footer-link{left:402px;font-size:15px;color:var(--white)}
.contact-item{left:572px;font-size:15px;line-height:25px;color:var(--white);display:flex;gap:12px;align-items:flex-start}
.contact-item svg{flex:none;margin-top:5px}
.newsletter{left:821px;top:4391px;width:266px;height:44px;border:1px solid #bbb;border-radius:22px}
.newsletter-hint{left:845px;top:4403px;font-size:14px;color:#ccc}
.btn-submit{left:996px;top:4395px;width:88px;height:36px;border-radius:18px;background:var(--yellow);font-family:"Raleway",sans-serif;font-weight:700;font-size:13px;color:var(--white);display:flex;align-items:center;justify-content:center}
.copyright{left:0;width:1200px;top:4588px;text-align:center;font-size:15px;color:var(--white)}
</style>
</head>
<body>

<!-- HEADER -->
<header class="abs site-header">
  <nav>
    <span class="abs nav-link" style="left:112px">Home</span>
    <span class="abs nav-link" style="left:195px">About Us</span>
    <span class="abs nav-link" style="left:301px">Services</span>
    <span class="abs nav-link" style="left:400px">Gallery</span>
    <span class="abs nav-link" style="left:745px">Blog</span>
    <span class="abs nav-link" style="left:818px">Contact</span>
  </nav>
  <svg class="abs search-icon" width="20" height="20" viewBox="0 0 20 20" aria-hidden="true"><circle cx="8" cy="8" r="6" fill="none" stroke="#f0b31b" stroke-width="2.5"/><line x1="12.5" y1="12.5" x2="18" y2="18" stroke="#f0b31b" stroke-width="2.5" stroke-linecap="round"/></svg>
  <div class="abs btn-login">LOG IN</div>
</header>
<div class="abs brand-badge"></div>
<div class="abs brand-dot"></div>
<div class="abs brand-name">DORVIK ELECTRIC Ltd</div>

<!-- HERO -->
<section>
  <div class="abs hero-photo" role="img" aria-label="Electrician in hard hat and gloves fitting a glowing light bulb"></div>
  <svg class="abs hero-shape" width="1200" height="110" viewBox="0 0 1200 110" aria-hidden="true">
    <polygon points="0,15 984,96 1200,24 1200,110 0,110" fill="#ffffff"/>
    <polygon points="0,15 984,80 1200,20 1200,28 984,98 0,27" fill="#f0b31b"/>
  </svg>
  <div class="abs head hero-kicker">WELCOME TO</div>
  <h1 class="abs head hero-title one">DORVIK</h1>
  <div class="abs head hero-title two">ELECTRIC</div>
  <p class="abs hero-copy">Lorem ipsum dolor sit amet, consectetur adipiscing elit, sed do eiusmod tempor incididunt ut</p>
  <div class="abs btn btn-start">GET STARTED</div>
  <div class="abs slider-dots"><span></span><span class="on"></span><span class="on"></span><span></span></div>
</section>

<!-- ABOUT -->
<section>
  <div class="abs about-photo-a" role="img" aria-label="Electrician in white hard hat working at a distribution panel"></div>
  <div class="abs about-panel"></div>
  <div class="abs about-photo-b" role="img" aria-label="Electrician on a rooftop holding a tablet at sunset"></div>
  <div class="abs eyebrow about-eyebrow">ABOUT US</div>
  <svg class="abs mini-rule" width="70" height="10" viewBox="0 0 70 10" aria-hidden="true"><line x1="0" y1="5" x2="28" y2="5" stroke="#f0b31b"/><circle cx="35" cy="5" r="3" fill="#f0b31b"/><line x1="42" y1="5" x2="70" y2="5" stroke="#f0b31b"/></svg>
  <h2 class="abs head about-title">Dorvik Electric</h2>
  <p class="abs about-copy">Lorem ipsum dolor sit amet, consectetur adipiscing elit, sed do eiusmod tempor incididunt ut labore et dolore magna aliqua. Ut enim ad minim veniam, quis nostrud exercitation ullamco laboris nisi ut aliquip ex ea commodo consequat. Duis aute irure dolor in reprehenderit in voluptate velit esse cillum dolore eu fugiat nulla pariatur. Excepteur sint occaecat cupidatat non proident, sunt in culpa qui officia deserunt mollit anim id est laborum.</p>
  <div class="abs btn btn-learn">LEARN MORE</div>
</section>

<!-- SERVICES -->
<section>
  <div class="abs services-band" role="img" aria-label="Faded background of an electrician at work"></div>
  <h2 class="abs section-title" style="top:1514px">OUR SERVICES</h2>
  <svg class="abs divider" style="top:1568px" viewBox="0 0 200 20" aria-hidden="true"><line x1="0" y1="10" x2="84" y2="10" stroke="#f0b31b" stroke-width="2"/><circle cx="100" cy="10" r="6" fill="#f0b31b"/><line x1="116" y1="10" x2="200" y2="10" stroke="#f0b31b" stroke-width="2"/></svg>
  <svg class="abs services-strip" width="1200" height="375" viewBox="0 0 1200 375">
    <defs>
      <linearGradient id="gHomes" x1="0" y1="0" x2="1" y2="1"><stop offset="0" stop-color="#8a5a32"/><stop offset=".35" stop-color="#c8955e"/><stop offset=".65" stop-color="#e6d6bc"/><stop offset="1" stop-color="#9a6a40"/></linearGradient>
      <linearGradient id="gRes" x1="0" y1="0" x2="0" y2="1"><stop offset="0" stop-color="#5e8fcf"/><stop offset=".3" stop-color="#a8c4e4"/><stop offset=".5" stop-color="#9a8a72"/><stop offset=".7" stop-color="#5f7a48"/><stop offset="1" stop-color="#2e2e30"/></linearGradient>
      <linearGradient id="gCom" x1="0" y1="0" x2="1" y2="1"><stop offset="0" stop-color="#0f2a6a"/><stop offset=".4" stop-color="#2f5fb4"/><stop offset=".7" stop-color="#7aa4e0"/><stop offset="1" stop-color="#1c3a80"/></linearGradient>
    </defs>
    <polygon role="img" aria-label="Custom home interior under construction" points="0,0 365,0 401,375 0,375" fill="url(#gHomes)"/>
    <polygon role="img" aria-label="Row of suburban family houses" points="370,0 807,0 848,375 406,375" fill="url(#gRes)"/>
    <polygon role="img" aria-label="Glass commercial office building" points="812,0 1200,0 1200,375 853,375" fill="url(#gCom)"/>
  </svg>
  <div class="abs service-label" style="left:11px">Custom Homes</div>
  <div class="abs service-label" style="left:441px">Residential</div>
  <div class="abs service-label" style="left:872px">Commercial</div>
  <div class="abs service-plus" style="left:161px">+</div>
  <div class="abs service-plus" style="left:591px">+</div>
  <div class="abs service-plus" style="left:1022px">+</div>
</section>

<!-- TESTIMONIALS -->
<section>
  <div class="abs testimonial-photo" role="img" aria-label="Electrician holding a yellow hard hat with a tool belt"></div>
  <h2 class="abs section-title" style="top:2202px">WHAT OUR CLIENTS SAY</h2>
  <svg class="abs divider" style="top:2254px" viewBox="0 0 200 20" aria-hidden="true"><line x1="0" y1="10" x2="84" y2="10" stroke="#f0b31b" stroke-width="2"/><circle cx="100" cy="10" r="6" fill="#f0b31b"/><line x1="116" y1="10" x2="200" y2="10" stroke="#f0b31b" stroke-width="2"/></svg>
  <div class="abs quote-mark">&#8220;</div>
  <p class="abs quote-copy">Lorem ipsum dolor sit amet, consectetur adipiscing elit, sed do eiusmod tempor incididunt ut labore et dolore magna aliqua. Ut enim ad minim veniam, quis nostrud exercitation ullamco laboris nisi ut aliquip ex ea commodo consequat. Duis aute irure dolor in reprehenderit in voluptate velit esse cillum dolore eu fugiat nulla pariatur. Excepteur sint occaecat cupidatat non proident, sunt in culpa qui officia deserunt mollit anim id est laborum.</p>
  <svg class="abs arrow" style="left:180px" width="26" height="24" viewBox="0 0 26 24" aria-hidden="true"><path d="M24 12H3M10 5 3 12l7 7" fill="none" stroke="#141414" stroke-width="2"/></svg>
  <svg class="abs arrow" style="left:982px" width="26" height="24" viewBox="0 0 26 24" aria-hidden="true"><path d="M2 12h21M16 5l7 7-7 7" fill="none" stroke="#f0b31b" stroke-width="2"/></svg>
  <div class="abs stars">★★★★★</div>
  <div class="abs client-name">MARCUS ELLERY</div>
  <div class="abs client-role">Managing Director</div>
</section>

<!-- PROJECTS -->
<section>
  <div class="abs projects-band" role="img" aria-label="Faded background of hanging bulbs on a yellow wash">
    <h2 class="abs section-title" style="top:70px">OUR PROJECTS</h2>
    <svg class="abs divider" style="top:122px" viewBox="0 0 200 20" aria-hidden="true"><line x1="0" y1="10" x2="84" y2="10" stroke="#fff" stroke-width="2"/><circle cx="100" cy="10" r="6" fill="#fff"/><line x1="116" y1="10" x2="200" y2="10" stroke="#fff" stroke-width="2"/></svg>
  </div>
  <div class="abs project-tile" style="left:112px;top:2897px;background:linear-gradient(125deg,#e8e4dc 0%,#3a3634 25%,#c89a3a 45%,#4a4a52 70%,#7a7e88 100%)" role="img" aria-label="Electrician with safety glasses testing a panel"></div>
  <div class="abs project-tile" style="left:446px;top:2897px;background:linear-gradient(150deg,#f4f4f6 0%,#d6d8dc 40%,#c8503a 58%,#7a7c82 78%,#b4b6ba 100%)" role="img" aria-label="Electrician fitting a ceiling light from a ladder"></div>
  <div class="abs project-tile" style="left:782px;top:2897px;background:linear-gradient(110deg,#8a4a32 0%,#b0684a 35%,#e8e0d4 55%,#a86a48 75%,#6a3e2c 100%)" role="img" aria-label="Electrician on a ladder against a brick wall"></div>
  <div class="abs project-tile" style="left:112px;top:3179px;background:linear-gradient(135deg,#f0c870 0%,#d89a3a 35%,#5a3a2a 55%,#e8b860 75%,#f2e0c0 100%)" role="img" aria-label="Gloved hands stripping electrical wires"></div>
  <div class="abs project-tile" style="left:446px;top:3179px;background:linear-gradient(160deg,#e6ecf4 0%,#f8f8fa 40%,#d8dadf 65%,#c04030 78%,#f0f0f2 100%)" role="img" aria-label="Power strip and tools on a workbench"></div>
  <div class="abs project-tile" style="left:782px;top:3179px;background:linear-gradient(120deg,#aec0d6 0%,#e8ecf0 35%,#e8a83a 55%,#5a7aa0 75%,#d8dce2 100%)" role="img" aria-label="Electrician on a step ladder installing wiring"></div>
</section>

<!-- BLOG -->
<section>
  <h2 class="abs section-title" style="top:3590px">LATEST BLOG</h2>
  <svg class="abs divider" style="top:3642px" viewBox="0 0 200 20" aria-hidden="true"><line x1="0" y1="10" x2="84" y2="10" stroke="#f0b31b" stroke-width="2"/><circle cx="100" cy="10" r="6" fill="#f0b31b"/><line x1="116" y1="10" x2="200" y2="10" stroke="#f0b31b" stroke-width="2"/></svg>

  <div class="abs blog-feature" role="img" aria-label="Smiling electrician in hard hat beside an electrical panel"></div>
  <article class="abs blog-card">
    <div class="abs blog-date" style="left:25px;top:28px">August 06,2022</div>
    <h3 class="abs blog-title" style="left:25px;top:58px">Sed ut perspiciatis unde omnis iste</h3>
    <p class="abs blog-copy" style="left:25px;top:96px;width:345px">Lorem ipsum dolor sit amet, consectetur adipiscing elit, sed do eiusmod tempor incididunt ut labore et dolore</p>
    <div class="abs read-more" style="left:25px;top:153px">READ MORE →</div>
    <div class="abs card-nav" style="left:421px;top:77px;background:var(--yellow)">›</div>
    <div class="abs card-nav" style="left:421px;top:120px;background:#b8b8b8">‹</div>
  </article>

  <div class="abs blog-thumb" style="top:3713px;background:linear-gradient(135deg,#3a5a8a 0%,#8aa0c0 30%,#d8c8a8 55%,#e8b840 72%,#4a4a50 100%)" role="img" aria-label="Electrician repairing a wall fitting"></div>
  <div class="abs blog-date" style="left:863px;top:3710px">August 06,2022</div>
  <h3 class="abs blog-title" style="left:863px;top:3740px;width:200px">Sed ut perspiciatis unde omnis iste</h3>
  <p class="abs blog-copy" style="left:863px;top:3800px;width:215px">Lorem ipsum dolor sit amet, consectetur adipiscing elit, sed do eiusmod tempor incididunt</p>
  <div class="abs read-more" style="left:863px;top:3872px">READ MORE →</div>

  <div class="abs blog-thumb" style="top:3917px;background:linear-gradient(120deg,#c89a5a 0%,#f0e8dc 30%,#8a6a4a 55%,#e8e4de 75%,#5a4a3a 100%)" role="img" aria-label="Electrician on a ladder hanging a pendant lamp"></div>
  <div class="abs blog-date" style="left:863px;top:3914px">August 06,2022</div>
  <h3 class="abs blog-title" style="left:863px;top:3944px;width:200px">Sed ut perspiciatis unde omnis iste</h3>
  <p class="abs blog-copy" style="left:863px;top:4004px;width:215px">Lorem ipsum dolor sit amet, consectetur adipiscing elit, sed do eiusmod tempor incididunt</p>
  <div class="abs read-more" style="left:863px;top:4076px">READ MORE →</div>
</section>

<!-- FOOTER -->
<footer>
  <svg class="abs footer-shape" width="1200" height="468" viewBox="0 0 1200 468" aria-hidden="true">
    <polygon points="0,92 230,18 1200,58 1200,468 0,468" fill="#141414"/>
    <polygon points="0,84 230,8 1200,50 1200,60 230,22 0,98" fill="#f0b31b"/>
  </svg>
  <div class="abs footer-dot"></div>
  <div class="abs footer-brand">DORVIK ELECTRIC Ltd</div>
  <span class="abs social" style="left:110px"></span>
  <span class="abs social" style="left:148px"></span>
  <span class="abs social" style="left:188px"></span>
  <span class="abs social" style="left:224px"></span>
  <span class="abs social" style="left:268px"></span>

  <h4 class="abs footer-title" style="left:402px">QUICK LINKS</h4>
  <span class="abs footer-link" style="top:4384px">Home</span>
  <span class="abs footer-link" style="top:4410px">About Us</span>
  <span class="abs footer-link" style="top:4435px">Services</span>
  <span class="abs footer-link" style="top:4460px">Gallery</span>
  <span class="abs footer-link" style="top:4487px">Blog</span>
  <span class="abs footer-link" style="top:4512px">Contact</span>

  <h4 class="abs footer-title" style="left:567px">CONTACT</h4>
  <div class="abs contact-item" style="top:4384px">
    <svg width="12" height="16" viewBox="0 0 12 16" aria-hidden="true"><path d="M6 0a6 6 0 0 0-6 6c0 4.5 6 10 6 10s6-5.5 6-10a6 6 0 0 0-6-6zm0 8.5A2.5 2.5 0 1 1 6 3.5a2.5 2.5 0 0 1 0 5z" fill="#fff"/></svg>
    <span>88 Cedar Bluff Rd<br>Nanaimo BC V9R 2K1</span>
  </div>
  <div class="abs contact-item" style="top:4446px">
    <svg width="14" height="14" viewBox="0 0 14 14" aria-hidden="true"><path d="M3 0 5 4 3.5 5.5a9 9 0 0 0 5 5L10 9l4 2-1 3C6 14 0 8 0 1z" fill="#fff"/></svg>
    <span>250-555-0147</span>
  </div>
  <div class="abs contact-item" style="top:4484px">
    <svg width="16" height="12" viewBox="0 0 16 12" aria-hidden="true"><rect width="16" height="12" rx="1" fill="#fff"/><path d="M0 1l8 6 8-6" fill="none" stroke="#141414" stroke-width="1.5"/></svg>
    <span>info@dorvikelectric.com</span>
  </div>

  <h4 class="abs footer-title" style="left:823px">NEWSLETTER SIGN UP</h4>
  <div class="abs newsletter"></div>
  <span class="abs newsletter-hint">Your Email</span>
  <div class="abs btn-submit">SUBMIT</div>

  <div class="abs copyright">©Copyrights 2022 Dorvik Electric &nbsp;&nbsp;|&nbsp;&nbsp; All Rights Reserved</div>
</footer>

</body>
</html>
```